Web design required

1-We need a web design for existing company based in New Zealand
2-We build residential house and light commercial
3-We has in-house designer which allow us can provide interior design
4-We modeling project before site construction, which enable both client and construction team to visually analysis whole project,

Target Market(s)

middle class residential house market
Ref: http://www.parvellbuilders.co.nz/

Industry/Entity Type

Construction Company

Number of Pages Required

1 page

Font styles to use
Sans Serif
Other font styles liked:
• Such as : Central Gothic or similar which has more design taste

Colors

Designer to choose colors to be used in the design.

Requirements
Must have
• Front sheet, contact information, sample project

```html
<!DOCTYPE html>
<html lang="en">
<head>
<meta charset="utf-8">
<title>Kestrel Homes</title>
<link rel="stylesheet" href="https://fonts.googleapis.com/css2?family=Mulish:wght@600;700;800&family=Open+Sans:wght@400;600;700&display=swap">
<style>
:root{
  --blue:#0b4fa8;
  --blue-deep:#0a3f8c;
  --blue-bright:#1f63c2;
  --ink:#333a40;
  --text:#5a5f66;
  --white:#ffffff;
  --line:#c9ced6;
  --red:#d8141c;
  --footer-dark:#2b2622;
}
*{margin:0;padding:0;box-sizing:border-box}
html,body{width:1200px;height:2356px;overflow:hidden}
body{position:relative;background:var(--white);font-family:"Open Sans",Arial,sans-serif;color:var(--text)}
.abs{position:absolute}

/* hero */
.hero{left:0;top:0;width:1200px;height:644px;overflow:hidden}
.hero-photo{position:absolute}
.hero-photo.p1{left:0;top:0;width:598px;height:322px;background:linear-gradient(160deg,#7a5a3a,#c89a62 55%,#6e4c2c)}
.hero-photo.p2{left:598px;top:0;width:602px;height:322px;background:linear-gradient(200deg,#8fb0c8,#9a6a44 45%,#5a4a3e)}
.hero-photo.p3{left:0;top:322px;width:598px;height:322px;background:linear-gradient(120deg,#1f3550,#3a8fc0 35%,#b79268 70%,#6b4a36)}
.hero-photo.p4{left:598px;top:322px;width:602px;height:322px;background:linear-gradient(210deg,#c9d3d6,#b49c82 50%,#5e4c40)}
.brand{display:flex;align-items:center;gap:12px;color:var(--white);font-family:"Mulish",sans-serif;font-weight:800;font-size:32px;letter-spacing:1px}
.brand-dot{width:48px;height:48px;border-radius:50%;background:var(--white)}
.hero .brand{position:absolute;left:97px;top:48px}
.nav{position:absolute;right:60px;top:62px;display:flex;gap:40px;list-style:none}
.nav a{color:var(--white);text-decoration:none;font-family:"Mulish",sans-serif;font-weight:700;font-size:16px}
.hero-badge{position:absolute;left:537px;top:226px;width:120px;height:120px;border-radius:50%;background:var(--white)}
.hero-title{position:absolute;left:0;width:1200px;top:416px;text-align:center;color:var(--white);font-family:"Open Sans",sans-serif;font-weight:700;font-size:60px;letter-spacing:1px;text-shadow:0 2px 8px rgba(0,0,0,.35)}

/* welcome */
.section-title{font-family:"Mulish",sans-serif;font-weight:800;color:var(--ink);font-size:31px;letter-spacing:1px}
.welcome-title{left:99px;top:734px}
.welcome-copy{left:99px;top:808px;width:484px;font-size:13px;line-height:24px}
.welcome-copy p+p{margin-top:24px}
.btn-more{left:99px;top:1046px;width:137px;height:41px;border:1px solid var(--line);border-radius:21px;display:flex;align-items:center;justify-content:center;gap:8px;font-family:"Mulish",sans-serif;font-weight:700;font-size:14px;color:var(--blue-deep)}
.btn-more svg{width:13px;height:13px}
.video{left:713px;top:728px;width:330px;height:376px}

/* services */
.services{left:0;top:1181px;width:1200px;height:351px}
.services-title{left:99px;top:1280px;color:var(--white);font-family:"Mulish",sans-serif;font-weight:800;font-size:32px;letter-spacing:1px}
.services-lead{left:99px;top:1352px;width:290px;color:var(--white);font-weight:600;font-size:20px;line-height:30px}
.service-label{color:var(--white);font-weight:700;font-size:17px;line-height:26px;text-shadow:0 1px 4px rgba(0,0,0,.5)}
.s1{left:482px;top:1360px}
.s2{left:746px;top:1362px}
.s3{left:1009px;top:1362px}

/* employment */
.employment-title{left:0;width:1200px;top:1614px;text-align:center}
.employment-copy{left:0;width:1200px;top:1683px;text-align:center;font-size:12.5px;line-height:21px}
.employment-copy a{color:var(--blue-deep);text-decoration:none}
.signup{left:419px;top:1763px;width:382px;height:34px;border:1px solid var(--line);border-radius:17px;overflow:hidden;display:flex}
.signup-field{flex:1;padding-left:24px;display:flex;align-items:center;font-size:12px;color:#7b8088}
.signup-send{width:102px;background:var(--blue-bright);color:var(--white);font-size:13px;display:flex;align-items:center;padding-left:16px;position:relative}
.signup-send svg{position:absolute;right:2px;top:2px;width:30px;height:30px}

/* footer */
.footer{left:0;top:1900px;width:1200px;height:378px}
.footer-badge{left:553px;top:1869px;width:88px;height:88px;border-radius:50%;background:var(--white);box-shadow:0 2px 6px rgba(0,0,0,.2);display:flex;align-items:center;justify-content:center}
.footer-badge span{width:44px;height:44px;border-radius:50%;background:var(--blue)}
.footer .brand{position:absolute}
.footer-brand{left:97px;top:2116px}
.footer-heading{color:var(--white);font-family:"Mulish",sans-serif;font-weight:800;font-size:16px;letter-spacing:.5px}
.contact-head{left:460px;top:2036px}
.company-head{left:737px;top:2036px}
.follow-head{left:930px;top:2036px}
.contact-list{left:460px;top:2082px;list-style:none;color:var(--white);font-size:12px}
.contact-list li{display:flex;gap:14px;align-items:flex-start;margin-bottom:16px;line-height:19px}
.contact-list svg{width:16px;height:16px;flex:none;margin-top:2px}
.company-list{left:737px;top:2084px;list-style:none}
.company-list li{font-size:11.5px;color:var(--white);margin-bottom:13px;display:flex;gap:10px;align-items:center}
.company-list li::before{content:"»";font-size:12px}
.social{left:932px;top:2088px;display:flex;gap:11px}
.social span{width:34px;height:34px;border-radius:50%;border:2px solid var(--white)}
.bottom-bar{left:0;top:2278px;width:1200px;height:78px;background:linear-gradient(90deg,var(--blue-deep),var(--blue-bright),var(--blue-deep));color:var(--white);font-size:12px;display:flex;align-items:center;justify-content:center}
</style>
</head>
<body>

<header class="hero abs">
  <div class="hero-photo p1" role="img" aria-label="Photo of a two-storey timber family home at dusk"></div>
  <div class="hero-photo p2" role="img" aria-label="Photo of a modern timber and concrete house with garage"></div>
  <div class="hero-photo p3" role="img" aria-label="Photo of a lit home with a swimming pool at dusk"></div>
  <div class="hero-photo p4" role="img" aria-label="Photo of a bright interior staircase with a potted palm"></div>
  <div class="brand"><span class="brand-dot"></span>KESTREL HOMES</div>
  <ul class="nav">
    <li><a href="#">HOME</a></li>
    <li><a href="#">SERVICES</a></li>
    <li><a href="#">ABOUT</a></li>
    <li><a href="#">PROJECTS</a></li>
    <li><a href="#">CONTACT</a></li>
  </ul>
  <div class="hero-badge"></div>
  <h1 class="hero-title">KESTREL HOMES</h1>
</header>

<h2 class="section-title welcome-title abs">WELCOME TO KESTREL HOMES</h2>
<div class="welcome-copy abs">
  <p>Kestrel Homes is dedicated to creating and renovating beautiful and the unusual buildings. We build residential house and light commercial.</p>
  <p>Kestrel Homes works with you to take dream houses off the blueprints and into reality. We have the knowledge and expertise to customise homes to suit you from unusual materials and designs to environment sensitive locations. We model project before site construction, which enable both client and construction team to visually analysis whole project.</p>
</div>
<a class="btn-more abs">READ MORE
  <svg viewBox="0 0 14 14"><circle cx="7" cy="7" r="7" fill="#0a3f8c"/><path d="M5.5 4 L9 7 L5.5 10" stroke="#fff" stroke-width="1.8" fill="none"/></svg>
</a>
<svg class="video abs" viewBox="0 0 330 376">
  <defs>
    <linearGradient id="videoFill" x1="0" y1="0" x2="1" y2="1">
      <stop offset="0" stop-color="#c9a77a"/>
      <stop offset=".5" stop-color="#9a5a34"/>
      <stop offset="1" stop-color="#6f9a4a"/>
    </linearGradient>
  </defs>
  <polygon points="165,2 328,96 328,280 165,374 2,280 2,96" fill="none" stroke="#0b4fa8" stroke-width="3"/>
  <polygon points="165,18 314,104 314,272 165,358 16,272 16,104" fill="url(#videoFill)" role="img" aria-label="Video still of a covered porch with timber chairs"/>
  <circle cx="165" cy="188" r="27" fill="#d8141c"/>
  <polygon points="156,174 181,188 156,202" fill="#fff"/>
</svg>

<section class="services abs">
  <svg width="1200" height="351" viewBox="0 0 1200 351">
    <defs>
      <linearGradient id="plan" x1="0" y1="0" x2="1" y2="1"><stop offset="0" stop-color="#d8dade"/><stop offset="1" stop-color="#9ea3a8"/></linearGradient>
      <linearGradient id="model" x1="0" y1="0" x2="0" y2="1"><stop offset="0" stop-color="#c3c6c8"/><stop offset="1" stop-color="#7c7e80"/></linearGradient>
      <linearGradient id="house" x1="0" y1="0" x2="0" y2="1"><stop offset="0" stop-color="#b89a78"/><stop offset=".6" stop-color="#8a6a4c"/><stop offset="1" stop-color="#5f8a3e"/></linearGradient>
    </defs>
    <rect width="1200" height="351" fill="#0b4fa8"/>
    <polygon points="377,0 655,0 700,175 655,351 377,351 432,175" fill="url(#plan)" role="img" aria-label="Photo of hands over construction plans"/>
    <polygon points="655,0 905,0 950,175 905,351 655,351 700,175" fill="url(#model)" role="img" aria-label="Rendered model of a building under construction with cranes"/>
    <polygon points="905,0 1140,0 1185,175 1140,351 905,351 950,175" fill="url(#house)" role="img" aria-label="Photo of a finished house with a green lawn"/>
    <polygon points="1140,0 1200,0 1200,351 1140,351 1185,175" fill="#0b4fa8"/>
  </svg>
</section>
<h2 class="services-title abs">OUR SERVICES</h2>
<p class="services-lead abs">We build residential house and light commercial.</p>
<div class="service-label s1 abs">Preconstruction<br>Planning</div>
<div class="service-label s2 abs">Construction<br>Modelling</div>
<div class="service-label s3 abs">Full Project<br>Management</div>

<h2 class="section-title employment-title abs">OUR EMPLOYMENT</h2>
<p class="employment-copy abs">To apply for a job with Kestrel Homes, please send a cover letter together with your C.V. to <a href="#">info@kestrelhomes.com</a><br>(or) For any inquiries, questions or commendations, please call or fill out the following form</p>
<div class="signup abs">
  <div class="signup-field">Enter Email Address</div>
  <div class="signup-send">Send
    <svg viewBox="0 0 30 30"><circle cx="15" cy="15" r="14" fill="#0a3f8c"/><path d="M11 7 L20 15 L11 23" stroke="#fff" stroke-width="3.5" fill="none"/></svg>
  </div>
</div>

<footer class="footer abs">
  <svg width="1200" height="378" viewBox="0 0 1200 378">
    <defs>
      <linearGradient id="lounge" x1="0" y1="0" x2="1" y2="1">
        <stop offset="0" stop-color="#3a332d"/><stop offset=".5" stop-color="#4a3f36"/><stop offset="1" stop-color="#2b2622"/>
      </linearGradient>
    </defs>
    <polygon points="0,64 597,16 1200,64 1200,378 0,378" fill="url(#lounge)" role="img" aria-label="Darkened photo of an open-plan living room with a spiral staircase"/>
    <polyline points="0,64 597,16 1200,64" fill="none" stroke="#0b4fa8" stroke-width="7"/>
  </svg>
  <div class="brand footer-brand" style="left:97px;top:216px"><span class="brand-dot" style="width:42px;height:42px"></span>KESTREL HOMES</div>
</footer>
<div class="footer-badge abs"><span></span></div>

<h3 class="footer-heading contact-head abs">CONTACT US</h3>
<ul class="contact-list abs">
  <li><svg viewBox="0 0 16 16"><path d="M8 1a5 5 0 0 0-5 5c0 4 5 9 5 9s5-5 5-9a5 5 0 0 0-5-5z" fill="none" stroke="#fff" stroke-width="1.3"/><circle cx="8" cy="6" r="1.8" fill="none" stroke="#fff" stroke-width="1.3"/></svg><span>18 Harbourview Road, Flat<br>Bush Auckland</span></li>
  <li><svg viewBox="0 0 16 16"><path d="M3 2h3l1.5 3.5-2 1.2a8 8 0 0 0 3.8 3.8l1.2-2L14 10v3a1 1 0 0 1-1 1A11 11 0 0 1 2 3a1 1 0 0 1 1-1z" fill="none" stroke="#fff" stroke-width="1.2"/></svg><span>0064 9 555 0142</span></li>
  <li><svg viewBox="0 0 16 16"><rect x="1.5" y="3.5" width="13" height="9" fill="none" stroke="#fff" stroke-width="1.2"/><path d="M1.5 3.5 8 9l6.5-5.5" fill="none" stroke="#fff" stroke-width="1.2"/></svg><span>info@kestrelhomes.com</span></li>
</ul>

<h3 class="footer-heading company-head abs">COMPANY</h3>
<ul class="company-list abs">
  <li>Home</li>
  <li>About Us</li>
  <li>Our Services</li>
  <li>Our Projects</li>
</ul>

<h3 class="footer-heading follow-head abs">FOLLOW US</h3>
<div class="social abs" aria-label="Social media links">
  <span></span><span></span><span></span><span></span>
</div>

<div class="bottom-bar abs">© Copyright 2017 Kestrel Homes. All Rights Reserved &nbsp;&nbsp;|&nbsp;&nbsp; Privacy Policy.</div>

</body>
</html>
```